Business Cards for company that supports physicians that do medical research

Need to create a business card for Qorvel Studies (www.qorvelstudies.example), a company devoted to supporting physicians who conduct medical research. The form of the card should match the message of research and information quest. I have provided the logo of the company as an uploaded file. Designs should be simple and slick aimed at very high end clients.

Target Market(s)

Medical doctors that are also researchers

Industry/Entity Type

Medical

Contact Information for Business Card

Should feature logo and fields for personal info:
Name/title
Phone /email

Font styles to use
Serif
Sans Serif

Requirements
Must have
• Qorvel logo and fields for personal info:
• Name: Bertrand Okonfu
• Title: VP Research and Senior Analyst
• Phone: 555-203-4719
• email: info@qorvelstudies.example
Nice to have
• Interesting cards that I've seen:
• 1- all black/charcoal or very dark background
• 2- Plastic - semi-transparent
• 3- non-standard height-width ratios
• 4- Functional cards -- USB drive incorporated
Should not have
• Too busy; needs to stay very simple

```html
<!DOCTYPE html>
<html lang="en">
<head>
<meta charset="utf-8">
<title>Qorvel Studies – Business Cards</title>
<link href="https://fonts.googleapis.com/css2?family=Open+Sans:wght@400;600&display=swap" rel="stylesheet">
<style>
  :root {
    --page-bg: #e8e5e2;
    --card-bg: #2a2828;
    --card-edge: #3a3838;
    --accent-blue: #2a8fd6;
    --brand-green: #5cbf4c;
    --text-light: #f2f2f2;
  }
  html, body {
    margin: 0;
    padding: 0;
    width: 1200px;
    height: 900px;
    overflow: hidden;
    background: var(--page-bg);
    font-family: "Open Sans", Arial, sans-serif;
  }
  .canvas {
    position: relative;
    width: 1200px;
    height: 900px;
  }
  .card {
    position: absolute;
    width: 556px;
    height: 342px;
    background: var(--card-bg);
    border: 1px solid var(--card-edge);
    box-sizing: border-box;
    color: var(--text-light);
  }
  .card-front { left: 238px; top: 62px; }
  .card-back  { left: 458px; top: 518px; }

  .person-name {
    position: absolute;
    left: 33px;
    top: 36px;
    margin: 0;
    font-size: 20px;
    font-weight: 600;
    color: var(--accent-blue);
  }
  .person-title {
    position: absolute;
    left: 33px;
    top: 65px;
    margin: 0;
    font-size: 14px;
    font-weight: 400;
  }
  .brand-name {
    position: absolute;
    margin: 0;
    font-weight: 600;
    color: var(--brand-green);
    white-space: nowrap;
    text-align: center;
  }
  .card-front .brand-name {
    left: 290px;
    top: 140px;
    width: 200px;
    font-size: 30px;
    line-height: 1.1;
  }
  .card-back .brand-name {
    left: 130px;
    top: 120px;
    width: 320px;
    font-size: 46px;
    line-height: 1.05;
  }
  .contact-list {
    position: absolute;
    left: 35px;
    top: 262px;
    margin: 0;
    padding: 0;
    list-style: none;
    font-size: 14px;
  }
  .contact-item {
    display: flex;
    align-items: center;
    height: 23px;
  }
  .contact-icon {
    width: 15px;
    height: 15px;
    margin-right: 11px;
    flex: none;
  }
  .website {
    position: absolute;
    left: 0;
    top: 270px;
    width: 556px;
    text-align: center;
    margin: 0;
    font-size: 14px;
    padding-left: 58px;
    box-sizing: border-box;
  }
</style>
</head>
<body>
<main class="canvas">

  <section class="card card-front" aria-label="Business card front">
    <h1 class="person-name">Bertrand Okonfu</h1>
    <p class="person-title">VP Research and Senior Analyst</p>
    <p class="brand-name">Qorvel<br>Studies</p>
    <ul class="contact-list">
      <li class="contact-item">
        <svg class="contact-icon" viewBox="0 0 15 15" aria-hidden="true">
          <rect width="15" height="15" rx="2" fill="var(--accent-blue)"/>
          <path d="M3 6 Q7.5 2 12 6 L10.5 7 L9.5 5.8 H5.5 L4.5 7 Z" fill="#fff"/>
          <rect x="4" y="8" width="7" height="4" rx="1" fill="#fff"/>
        </svg>
        555-203-4719
      </li>
      <li class="contact-item">
        <svg class="contact-icon" viewBox="0 0 15 15" aria-hidden="true">
          <rect width="15" height="15" rx="2" fill="var(--accent-blue)"/>
          <rect x="3" y="4.5" width="9" height="6.5" fill="#fff"/>
          <path d="M3 4.5 L7.5 8 L12 4.5" fill="none" stroke="var(--accent-blue)" stroke-width="1"/>
        </svg>
        info@qorvelstudies.example
      </li>
    </ul>
  </section>

  <section class="card card-back" aria-label="Business card back">
    <p class="brand-name">Qorvel<br>Studies</p>
    <p class="website">www.qorvelstudies.example</p>
  </section>

</main>
</body>
</html>
```